Design a single page Shopify store web page

We are looking to have a page designed for a single page Shopify store with 2 products. We already have a basic structure that we like, though we are open to suggestions. We are looking for somebody to provide a design/color scheme that we can then implement using Shopify's templating system. We can handle the implementation(HTML / CSS / jS) as we already have 2 web developers on the team, but have not been able to find a design we liked.

The job would consist of providing a mockup (photoshop or otherwise) and any vector graphics you choose to create for the site (we can provide product photos and other images).

You can also look at http://brickdune.com.au for some of our design direction we have used so far

Target Market(s)

Young Australian Males (18 - 49)

Industry/Entity Type

Store

Number of Pages Required

1 page

Font styles to use
Serif
Sans Serif

Requirements
Must have
• Single Page Design
• E-commerce Product Purchase
• Manly (whatever interpretation of that you have)

```html
<!DOCTYPE html>
<html lang="en">
<head>
<meta charset="utf-8">
<title>Brick Dune — Automate Your Life</title>
<link rel="stylesheet" href="https://fonts.googleapis.com/css2?family=Montserrat:wght@400;500;600;700&family=Nunito+Sans:wght@400;600;700&display=swap">
<style>
:root{
  --navy:#1b2635;
  --navy-deep:#141d29;
  --red:#e2544c;
  --red-card:#d2463f;
  --ink:#1d2430;
  --grey:#6d7480;
  --white:#ffffff;
  --light:#c9ced6;
}
*{margin:0;padding:0;box-sizing:border-box}
html,body{width:1200px;height:3255px;overflow:hidden}
body{position:relative;background:var(--white);font-family:"Nunito Sans",Arial,sans-serif;color:var(--ink)}
.abs{position:absolute}
h1,h2,h3,.display{font-family:"Montserrat",Arial,sans-serif}

/* nav */
.topbar{left:0;top:0;width:1200px;height:100px;background:var(--navy)}
.brand{left:170px;top:24px;display:flex;align-items:center;gap:16px}
.brand-mark{width:52px;height:52px;border-radius:50%;border:2px solid var(--light)}
.brand-name{font-family:"Montserrat",sans-serif;font-weight:500;font-size:38px;letter-spacing:1px;color:var(--light)}
.menu{left:563px;top:41px;display:flex;font-family:"Montserrat",sans-serif;font-size:12px;font-weight:500;color:var(--white)}
.menu a{color:inherit;text-decoration:none;margin-right:44px}
.menu a.signup{color:var(--red);text-decoration:underline;margin-right:0}

/* hero */
.hero{left:0;top:100px;width:1200px;height:682px;background:var(--red);overflow:hidden}
.hero-photo{left:0;top:0;width:1200px;height:682px}
.hero-title{left:521px;top:140px;width:534px;color:var(--navy);font-weight:700;font-size:64px;line-height:82px;white-space:nowrap}
.hero-title .l2{text-align:right}
.hero-sub{left:455px;top:308px;width:600px;text-align:right;font-family:"Montserrat",sans-serif;font-weight:700;font-size:29px;line-height:54px;color:var(--white);white-space:nowrap}
.hero-sub .dark{color:var(--navy)}
.cta{left:733px;top:512px;width:236px;height:82px;background:var(--navy);color:var(--white);font-family:"Montserrat",sans-serif;font-weight:700;font-size:30px;display:flex;align-items:center;justify-content:center;box-shadow:0 6px 0 rgba(0,0,0,.18);white-space:nowrap}
.dots{left:853px;top:634px;display:flex;gap:4px}
.dots span{width:16px;height:16px;border-radius:50%;background:var(--white);border:3px solid var(--navy)}
.dots span.on{background:var(--navy)}

/* section headings */
.section-title{left:0;width:1200px;text-align:center;font-family:"Montserrat",sans-serif;font-weight:500;font-size:40px}
.rule{left:570px;width:60px;height:4px;background:var(--red)}

/* how it works */
.step{width:300px;text-align:center}
.step-circle{width:164px;height:164px;border-radius:50%;border:5px solid var(--red);margin:0 auto;display:flex;align-items:center;justify-content:center}
.step h3{font-family:"Nunito Sans",sans-serif;font-weight:600;font-size:22px;margin-top:36px}
.step p{font-size:11px;color:var(--grey);line-height:18px;margin:12px auto 0;width:240px}

/* plans */
.plans{left:0;top:1258px;width:1200px;height:658px;background:var(--red)}
.plan-card{top:1395px;width:446px;height:342px;background:var(--red-card)}
.plan-card h3{position:absolute;left:0;top:16px;width:100%;text-align:center;color:var(--white);font-weight:600;font-size:26px}
.plan-photo{left:34px;top:62px;width:240px;height:240px}
.plan-tag{left:286px;width:122px;height:38px;font-size:12px;padding:10px 12px}
.plan-tag.light{top:62px;background:var(--white);color:var(--grey);border:2px solid #eee}
.plan-tag.dark{top:106px;background:#3a3d45;color:var(--white)}
.plan-price{left:286px;top:168px;width:122px;text-align:center;color:var(--white);font-family:"Montserrat",sans-serif;font-weight:700;font-size:50px}
.plan-buy{left:286px;top:246px;width:122px;height:56px;background:var(--navy);color:var(--white);font-family:"Montserrat",sans-serif;font-weight:700;font-size:22px;display:flex;align-items:center;justify-content:center}
.perks{left:137px;top:1762px;width:926px;height:78px;background:var(--red-card);display:flex;align-items:center;justify-content:center;gap:30px;font-family:"Montserrat",sans-serif;font-weight:600;font-size:15px;color:var(--white)}
.perks span{display:flex;align-items:center;gap:10px}

/* faq */
.faq-item{width:300px;text-align:center}
.faq-item svg{display:block;margin:0 auto}
.faq-item h3{font-family:"Nunito Sans",sans-serif;font-weight:600;font-size:21px;color:var(--red);line-height:25px;margin-top:18px}
.faq-item p{font-size:11px;line-height:21px;color:var(--grey);margin:14px auto 0;width:250px}

/* about */
.about{left:0;top:2882px;width:1200px;height:275px;background:var(--navy)}
.about h2{position:absolute;left:0;top:34px;width:100%;text-align:center;color:var(--white);font-weight:500;font-size:40px}
.about .rule{top:96px}
.about p{position:absolute;left:160px;top:124px;width:880px;text-align:center;color:var(--white);font-size:12px;line-height:22px}

/* footer */
.footer{left:0;top:3157px;width:1200px;height:98px;background:var(--navy-deep);color:var(--white)}
.footer-links{left:170px;top:28px;font-size:12px;font-weight:600}
.footer-copy{left:170px;top:58px;font-size:10px;color:var(--light)}
.social{left:650px;top:30px;display:flex;gap:8px}
.social span,.pay span{height:36px;padding:0 8px;display:flex;align-items:center;font-family:"Nunito Sans",sans-serif;font-weight:700;font-size:11px;color:var(--white);background:#2f5a8c}
.pay{left:870px;top:32px;display:flex;gap:8px}
.pay span{height:32px;background:#3b4a5e}
</style>
</head>
<body>

<header class="abs topbar">
  <div class="abs brand"><span class="brand-mark"></span><span class="brand-name">BRICK DUNE</span></div>
  <nav class="abs menu">
    <a href="#how">HOW IT WORKS</a><a href="#plans">PLANS</a><a href="#faq">FAQ</a><a href="#about">ABOUT US</a><a class="signup" href="#plans">SIGN UP NOW</a>
  </nav>
</header>

<section class="abs hero">
  <svg class="abs hero-photo" viewBox="0 0 1200 682" role="img" aria-label="Photo of a man modelling black boxer briefs">
    <defs>
      <linearGradient id="heroShade" x1="0" y1="0" x2="1" y2="1">
        <stop offset="0" stop-color="#2a3a52"/><stop offset="1" stop-color="#1a2638"/>
      </linearGradient>
    </defs>
    <polygon points="0,0 435,0 630,682 0,682" fill="url(#heroShade)"/>
  </svg>
  <h1 class="abs hero-title"><div class="l1">AUTOMATE</div><div class="l2">YOUR LIFE</div></h1>
  <p class="abs hero-sub"><span class="dark">NEW</span> UNDERWEAR AND SOCKS<br>DELIVERED TO YOUR DOOR<br><span class="dark">WHEN YOU NEED IT</span></p>
  <a class="abs cta">YES PLEASE!!</a>
  <div class="abs dots"><span></span><span></span><span></span><span class="on"></span></div>
</section>

<section id="how">
  <h2 class="abs section-title" style="top:834px">HOW IT WORKS</h2>
  <div class="abs rule" style="top:890px"></div>
  <div class="abs step" style="left:143px;top:938px">
    <div class="step-circle"><svg width="70" height="70" viewBox="0 0 24 24"><path d="M2 11 22 3 16 21 11 14Z" fill="var(--ink)"/><path d="M11 14 22 3" stroke="#fff" stroke-width="1.2"/></svg></div>
    <h3>Choose a Plan</h3>
    <p>There will be plans for all budgets and styles.</p>
  </div>
  <div class="abs step" style="left:447px;top:938px">
    <div class="step-circle"><svg width="70" height="70" viewBox="0 0 24 24"><path d="M9 3a1.5 1.5 0 0 1 3 0v7l5 1c1.5.4 2 1.4 2 2.6L18 21H9l-4-6c-.6-1 .6-2.2 1.6-1.4L9 15Z" fill="var(--ink)"/></svg></div>
    <h3>Choose How Often</h3>
    <p>Decide whether you would like to receive new packages every 3 or 6 months.</p>
  </div>
  <div class="abs step" style="left:768px;top:938px">
    <div class="step-circle"><svg width="70" height="70" viewBox="0 0 24 24"><path d="M3 11h18v10H3Z" fill="var(--ink)"/><path d="M3 11 6 7h4l2 4M21 11l-3-4h-4l-2 4" fill="none" stroke="var(--ink)" stroke-width="1.5"/><path d="M12 1v6M9.5 4.5 12 7l2.5-2.5" fill="none" stroke="var(--ink)" stroke-width="1.6"/></svg></div>
    <h3>Choose How Often</h3>
    <p>We'll send out your first pack right away and then again every 3 or 6 months.</p>
  </div>
</section>

<section id="plans" class="abs plans">
  <h2 class="abs section-title" style="top:40px;color:var(--white)">PLANS</h2>
  <div class="abs rule" style="top:100px;background:var(--white)"></div>
</section>
<article class="abs plan-card" style="left:137px">
  <h3>Comfort</h3>
  <svg class="abs plan-photo" viewBox="0 0 240 240" role="img" aria-label="Photo of red socks on a grey floor"><rect width="240" height="240" fill="#55585c"/></svg>
  <div class="abs plan-tag light">Lorem ipsumd</div>
  <div class="abs plan-tag dark">Lorem ipsumd</div>
  <div class="abs plan-price">$30</div>
  <a class="abs plan-buy">GET IT!</a>
</article>
<article class="abs plan-card" style="left:616px">
  <h3>Style</h3>
  <svg class="abs plan-photo" viewBox="0 0 240 240" role="img" aria-label="Photo of a man in white boxer briefs"><rect width="240" height="240" fill="#8a6a5a"/></svg>
  <div class="abs plan-tag light">Lorem ipsumd</div>
  <div class="abs plan-tag dark">Lorem ipsumd</div>
  <div class="abs plan-price">$30</div>
  <a class="abs plan-buy">GET IT!</a>
</article>
<div class="abs perks">
  <span><svg width="18" height="14" viewBox="0 0 18 14"><path d="M2 7l5 5 9-10" fill="none" stroke="#fff" stroke-width="3"/></svg>FREE SHIPPING</span>
  <span><svg width="18" height="14" viewBox="0 0 18 14"><path d="M2 7l5 5 9-10" fill="none" stroke="#fff" stroke-width="3"/></svg>EASY RETURNS</span>
  <span><svg width="18" height="14" viewBox="0 0 18 14"><path d="M2 7l5 5 9-10" fill="none" stroke="#fff" stroke-width="3"/></svg>CANCEL WHENEVER</span>
  <span><svg width="18" height="14" viewBox="0 0 18 14"><path d="M2 7l5 5 9-10" fill="none" stroke="#fff" stroke-width="3"/></svg>SATISFACTION GUARANTEED</span>
</div>

<section id="faq">
  <h2 class="abs section-title" style="top:1966px">FAQ</h2>
  <div class="abs rule" style="top:2022px"></div>

  <div class="abs faq-item" style="left:143px;top:2052px">
    <svg width="80" height="80" viewBox="0 0 24 24"><path d="M4 5h9M4 5v15h15v-8" fill="none" stroke="var(--ink)" stroke-width="2"/><path d="M10 14l1-3 8-8 2 2-8 8Z" fill="var(--ink)"/></svg>
    <h3>What is a Brick Dune Plan</h3>
    <p>Donec sed odio dui. Nulla vitae elit libero, a pharetra augue. Nullam id dolor id nibh ultri cies vehicula ut id elit integer.</p>
  </div>
  <div class="abs faq-item" style="left:447px;top:2052px">
    <svg width="80" height="80" viewBox="0 0 24 24"><circle cx="12" cy="9" r="6.5" fill="var(--ink)"/><circle cx="12" cy="9" r="3.5" fill="none" stroke="#fff" stroke-width="1.2"/><path d="M8 14l-2 8 3-2 2 2 1-6M16 14l2 8-3-2-2 2-1-6" fill="var(--ink)"/></svg>
    <h3>What is your<br>Satisfaction Guarantee?</h3>
    <p>Donec sed odio dui. Nulla vitae elit libero, a pharetra augue. Nullam id dolor id nibh ultri cies vehicula ut id elit integer.</p>
  </div>
  <div class="abs faq-item" style="left:750px;top:2052px">
    <svg width="90" height="80" viewBox="0 0 27 24"><path d="M1 6h16v11H1Z" fill="var(--ink)"/><path d="M17 9h5l4 4v4h-9Z" fill="var(--ink)"/><circle cx="6" cy="19" r="2.5" fill="var(--ink)"/><circle cx="21" cy="19" r="2.5" fill="var(--ink)"/><text x="9" y="13.5" text-anchor="middle" font-family="Montserrat,sans-serif" font-size="5" font-weight="700" fill="#fff">FREE</text></svg>
    <h3>Shipping Policy</h3>
    <p>Donec sed odio dui. Nulla vitae elit libero, a pharetra augue. Nullam id dolor id nibh ultri cies vehicula ut id elit integer.</p>
  </div>

  <div class="abs faq-item" style="left:143px;top:2323px">
    <svg width="80" height="80" viewBox="0 0 24 24"><path d="M4 20l1-5L16 4l4 4L9 19Z" fill="none" stroke="var(--ink)" stroke-width="2.2"/><path d="M14 6l4 4" stroke="var(--ink)" stroke-width="2.2"/></svg>
    <h3>What Do i get with my<br>Brick Dune Plan</h3>
    <p>Donec sed odio dui. Nulla vitae elit libero, a pharetra augue. Nullam id dolor id nibh ultri cies vehicula ut id elit integer.</p>
  </div>
  <div class="abs faq-item" style="left:447px;top:2323px">
    <svg width="80" height="80" viewBox="0 0 24 24"><path d="M4 12V8h13M14 5l3 3-3 3M20 12v4H7M10 19l-3-3 3-3" fill="none" stroke="var(--ink)" stroke-width="3"/></svg>
    <h3>Returns Policy</h3>
    <p>Donec sed odio dui. Nulla vitae elit libero, a pharetra augue. Nullam id dolor id nibh ultri cies vehicula ut id elit integer.</p>
  </div>
  <div class="abs faq-item" style="left:750px;top:2323px">
    <svg width="80" height="80" viewBox="0 0 24 24"><path d="M3 8l5 4 4-6 4 6 5-4-2 10H5Z" fill="var(--ink)"/><rect x="5" y="19" width="14" height="2" fill="var(--ink)"/></svg>
    <h3>What Brands do you<br>Stock</h3>
    <p>Donec sed odio dui. Nulla vitae elit libero, a pharetra augue. Nullam id dolor id nibh ultri cies vehicula ut id elit integer.</p>
  </div>

  <div class="abs faq-item" style="left:143px;top:2610px">
    <svg width="80" height="80" viewBox="0 0 24 24"><path d="M1 5h3l3 10h11l2-7H6" fill="none" stroke="var(--ink)" stroke-width="2"/><circle cx="9" cy="19" r="1.8" fill="var(--ink)"/><circle cx="16" cy="19" r="1.8" fill="var(--ink)"/><circle cx="18" cy="5" r="4" fill="var(--ink)"/><path d="M16.5 3.5l3 3M19.5 3.5l-3 3" stroke="#fff" stroke-width="1.2"/></svg>
    <h3>What Is Your<br>Cancellation Policy</h3>
    <p>Donec sed odio dui. Nulla vitae elit libero, a pharetra augue. Nullam id dolor id nibh ultri cies vehicula ut id elit integer.</p>
  </div>
  <div class="abs faq-item" style="left:447px;top:2610px">
    <svg width="80" height="80" viewBox="0 0 24 24"><path d="M3 6h12v12H3Z" fill="none" stroke="var(--ink)" stroke-width="2"/><path d="M3 2h12M19 6v12M17 8l2-2 2 2M17 16l2 2 2-2" fill="none" stroke="var(--ink)" stroke-width="1.8"/></svg>
    <h3>What about Sizing</h3>
    <p>Donec sed odio dui. Nulla vitae elit libero, a pharetra augue. Nullam id dolor id nibh ultri cies vehicula ut id elit integer.</p>
  </div>
  <div class="abs faq-item" style="left:750px;top:2610px">
    <svg width="80" height="80" viewBox="0 0 24 24"><path d="M2 7l12-4 2 6-12 4Z" fill="var(--ink)"/><ellipse cx="17" cy="13" rx="5" ry="1.8" fill="var(--ink)"/><ellipse cx="17" cy="16.5" rx="5" ry="1.8" fill="var(--ink)"/><ellipse cx="17" cy="20" rx="5" ry="1.8" fill="var(--ink)"/></svg>
    <h3>How does Payment<br>Work</h3>
    <p>Donec sed odio dui. Nulla vitae elit libero, a pharetra augue. Nullam id dolor id nibh ultri cies vehicula ut id elit integer.</p>
  </div>
</section>

<section id="about" class="abs about">
  <h2>ABOUT US</h2>
  <div class="abs rule"></div>
  <p>Lorem ipsum dolor sit amet, consectetur adipiscing elit, sed do eiusmod tempor incididunt ut labore et dolore magna aliqua. Ut enim ad minim veniam, quis nostrud exercitation ullamco laboris nisi ut aliquip ex ea commodo consequat. Duis aute irure dolor in reprehenderit in voluptate velit esse cillum dolore eu fugiat nulla pariatur. Excepteur sint occaecat cupidatat non proident, sunt in culpa qui officia deserunt mollit anim id est laborum. Lorem ipsum dolor sit amet, consectetur adipiscing elit, sed do eiusmod tempor incididunt ut labore et dolore magna aliqua. Ut enim ad minim veniam, quis nostrud exercitation ullamco laboris nisi ut aliquip ex ea commodo consequat.</p>
</section>

<footer class="abs footer">
  <div class="abs footer-links">Shipping/ Returns / Payment / Terms / Privacy</div>
  <div class="abs footer-copy">Brick Dune 2014 all copyrights are reserved</div>
  <div class="abs social"><span>Pals</span><span>Chirp</span><span>Blogr</span><span>Snaps</span></div>
  <div class="abs pay"><span>Amplex</span><span>Vexa</span><span>Mintcard</span></div>
</footer>

</body>
</html>
```